Business card for marketing analytics company

Need a business card for new company. I have a logo already that I want to be built into the card and should use those colours

Company is called steered by tallies
Design must bring steered by tallies to life not be a card that could be for anyone with a logo put on it.

Like the front to be fairly clean and uncluttered bringing the logo out with a suitable design on the back of the card.

The logo represents a compass and business growth so those themes along with numbers, analytics , data are appropriate.
I'm often working with creative industries so also needs to reflect the creative side of analytics rather than be very corporate looking.

Target Market(s)

Ad agency, media agency, consumer goods clients

Industry/Entity Type

Market Research

Contact Information for Business Card

Needs to include name, title, email and phone number

Colors
f78f20
f68d4d
ec1f27

Requirements
Must have
• Must bring steered by tallies to life not be a card that could be for anyone with a logo put on it.
• Logo, Correct colours
• Like a design on the back that relates to company name
• Designs for both sides
Should not have
• Please do not just submit logo and a coloured card.
• It needs to have a design element to it
• No black background
• No clear cards - needs front & back

```html
<!DOCTYPE html>
<html lang="en">
<head>
<meta charset="utf-8">
<title>Steered by Tallies — Business Card</title>
<link rel="stylesheet" href="https://fonts.googleapis.com/css2?family=Montserrat:wght@500;600;700&display=swap">
<style>
  :root {
    --backdrop: #e9e7e4;
    --brand-red: #ec1f27;
    --deep-red: #c1212a;
    --brand-orange: #f78f20;
    --ink: #3d4a55;
    --paper: #ffffff;
    --card-shadow: 0 18px 40px rgba(0, 0, 0, 0.18);
  }
  * { box-sizing: border-box; margin: 0; padding: 0; }
  html, body {
    width: 1200px;
    height: 1000px;
    overflow: hidden;
    background: var(--backdrop);
    font-family: "Montserrat", sans-serif;
  }
  .sheet {
    width: 1200px;
    height: 1000px;
    display: flex;
    flex-direction: column;
    align-items: center;
    justify-content: center;
    gap: 44px;
  }
  .card {
    position: relative;
    width: 700px;
    height: 400px;
    border-radius: 20px;
    overflow: hidden;
    box-shadow: var(--card-shadow);
  }

  /* Logo side */
  .card--brand {
    background: var(--deep-red);
    color: var(--paper);
  }
  .brand-lockup {
    position: absolute;
    left: 170px;
    top: 118px;
    display: flex;
    align-items: center;
    gap: 30px;
  }
  .brand-lockup__dot {
    width: 120px;
    height: 120px;
    border: 5px solid var(--paper);
    border-radius: 50%;
  }
  .brand-lockup__name {
    font-weight: 600;
    font-size: 40px;
    line-height: 1.05;
  }
  .card--brand .site {
    position: absolute;
    left: 0;
    right: 0;
    bottom: 40px;
    text-align: center;
    font-weight: 500;
    font-size: 15px;
    letter-spacing: 1.5px;
  }

  /* Contact side */
  .card--contact {
    background: var(--paper);
    display: flex;
  }
  .contact-brand {
    width: 330px;
    display: flex;
    align-items: center;
    justify-content: center;
    gap: 16px;
  }
  .contact-brand__dot {
    width: 76px;
    height: 76px;
    border: 4px solid var(--brand-orange);
    border-radius: 50%;
    flex-shrink: 0;
  }
  .contact-brand__name {
    font-weight: 600;
    font-size: 27px;
    line-height: 1.05;
    color: var(--ink);
  }
  .contact-panel {
    position: relative;
    flex: 1;
    background: var(--brand-red);
    color: var(--paper);
    padding: 70px 40px 0 58px;
  }
  .contact-panel::before {
    content: "";
    position: absolute;
    left: -14px;
    top: 84px;
    border-top: 12px solid transparent;
    border-bottom: 12px solid transparent;
    border-right: 14px solid var(--brand-red);
  }
  .person__name {
    font-weight: 700;
    font-size: 26px;
    letter-spacing: 0.5px;
  }
  .person__role {
    font-weight: 600;
    font-size: 14px;
    letter-spacing: 0.5px;
    margin-top: 4px;
  }
  .details {
    list-style: none;
    margin-top: 22px;
  }
  .details li {
    display: flex;
    align-items: center;
    gap: 12px;
    font-weight: 500;
    font-size: 16px;
    line-height: 26px;
  }
  .details svg { width: 15px; height: 15px; flex-shrink: 0; }
  .address {
    margin-top: 24px;
    font-weight: 500;
    font-size: 16px;
    line-height: 24px;
  }
</style>
</head>
<body>
<main class="sheet">

  <section class="card card--brand" aria-label="Card back">
    <div class="brand-lockup">
      <div class="brand-lockup__dot"></div>
      <div class="brand-lockup__name">Steered by<br>Tallies</div>
    </div>
    <p class="site">www.yoursitename.com</p>
  </section>

  <section class="card card--contact" aria-label="Card front">
    <div class="contact-brand">
      <div class="contact-brand__dot"></div>
      <div class="contact-brand__name">Steered by<br>Tallies</div>
    </div>
    <div class="contact-panel">
      <h1 class="person__name">DANA WHITFIELD</h1>
      <p class="person__role">FOUNDER</p>
      <ul class="details">
        <li>
          <svg viewBox="0 0 16 16" aria-hidden="true"><path fill="#fff" d="M2 6c0-2 2-3 6-3s6 1 6 3v1h-3V5.5H5V7H2zM4 8h8l1 5H3zm4 1.2a1.6 1.6 0 1 0 0 3.2 1.6 1.6 0 0 0 0-3.2z"/></svg>
          000 000 0000
        </li>
        <li>
          <svg viewBox="0 0 16 16" aria-hidden="true"><rect x="1" y="3" width="14" height="10" fill="#fff"/><path d="M1.5 3.5 8 9l6.5-5.5" fill="none" stroke="#ec1f27" stroke-width="1.4"/></svg>
          info@yourmail.com
        </li>
        <li>
          <svg viewBox="0 0 16 16" aria-hidden="true"><circle cx="9.5" cy="6.5" r="4" fill="none" stroke="#fff" stroke-width="2"/><path d="M6.5 9.5 2 14" stroke="#fff" stroke-width="2.4" stroke-linecap="round"/></svg>
          www.yoursite.com
        </li>
      </ul>
      <p class="address">your street address,<br>suite-123, country-1230</p>
    </div>
  </section>

</main>
</body>
</html>
```